Business card design needed

My business is in Matchmaking. My objective is to find the most compatible partner for my clients....basically I'm in the love and happiness industry bringing two people together for a lasting loving relationship.

I envision the design to be something with 2 people who are in love looking happy or even a silhouette.....I don't really know, I'm open to ideas.....maybe no picture at all, but I want it to be classy :-)

I do have a logo which I will upload. You can also go to my website to give you an idea on the colours and the design if that helps, however the website is not finished yet, it should be up by today or tomorrow. If the website has a heart with swirls on the upper left hand corner, that is the old website, please ignore that one. The one that will be up shortly has a picture frame on the home page with my logo that will be in the file I will upload on this page.

Target Market(s)

There are three categories: Over 45, Asian and Western and same sex, but would be able to afford to hire a matchmaker

Contact Information for Business Card

The Tidewell Bureau
Helping You Find The "One"
Mavis Ellery
Matchmaker
0492 517 264
info@tidewellbureau.com.au
www.tidewellbureau.com.au

```html
<!DOCTYPE html>
<html lang="en">
<head>
<meta charset="utf-8">
<title>The Tidewell Bureau — Business Card</title>
<link rel="stylesheet" href="https://fonts.googleapis.com/css2?family=Open+Sans:wght@600;700;800&display=swap">
<style>
  :root {
    --backdrop: #e9e6e2;
    --cream: #fbf7dc;
    --plum: #7b5b76;
    --plum-deep: #6a4b67;
    --plum-text: #6b4a6e;
    --teal: #8ebcb4;
    --band-text: #f6efbe;
    --photo-light: #9a9a98;
    --photo-dark: #262626;
  }
  * { box-sizing: border-box; margin: 0; padding: 0; }
  html, body { width: 1200px; height: 1000px; overflow: hidden; }
  body {
    background: var(--backdrop);
    font-family: "Open Sans", Arial, sans-serif;
    position: relative;
  }
  .card {
    position: absolute;
    left: 100px;
    top: 214px;
    width: 1000px;
    height: 572px;
    display: flex;
    background: var(--cream);
    box-shadow: 0 10px 30px rgba(0,0,0,0.18);
    overflow: hidden;
  }
  .card__photo {
    width: 370px;
    height: 100%;
    background: radial-gradient(ellipse at 55% 45%, var(--photo-light) 0%, #5d5d5b 45%, var(--photo-dark) 100%);
    border-right: 7px solid var(--teal);
    flex-shrink: 0;
  }
  .card__content {
    flex: 1;
    display: flex;
    flex-direction: column;
  }
  .card__brand {
    height: 262px;
    display: flex;
    flex-direction: column;
    align-items: center;
    justify-content: center;
    gap: 18px;
    padding-top: 20px;
  }
  .brand__name {
    display: flex;
    align-items: center;
    gap: 14px;
    font-weight: 700;
    font-size: 44px;
    color: var(--plum-text);
    letter-spacing: 0.5px;
  }
  .brand__dot {
    width: 22px;
    height: 22px;
    border-radius: 50%;
    background: var(--teal);
  }
  .brand__tagline {
    font-weight: 800;
    font-size: 30px;
    color: var(--plum-text);
    letter-spacing: -0.3px;
  }
  .card__details {
    flex: 1;
    background: linear-gradient(180deg, var(--plum) 0%, var(--plum-deep) 100%);
    color: var(--band-text);
    padding: 40px 0 0 54px;
  }
  .details__name {
    font-weight: 800;
    font-size: 42px;
    line-height: 1.05;
  }
  .details__role {
    font-weight: 700;
    font-size: 28px;
    line-height: 1.2;
    margin-bottom: 22px;
  }
  .details__contact {
    list-style: none;
    font-weight: 700;
    font-size: 28px;
    line-height: 1.22;
  }
</style>
</head>
<body>
  <article class="card">
    <div class="card__photo" role="img" aria-label="Black and white photograph of two clasped hands, one wearing a diamond engagement ring and a bracelet"></div>
    <div class="card__content">
      <header class="card__brand">
        <div class="brand__name"><span class="brand__dot"></span>The Tidewell Bureau</div>
        <p class="brand__tagline">Helping You Find The "One"</p>
      </header>
      <section class="card__details">
        <h1 class="details__name">Mavis Ellery</h1>
        <p class="details__role">Matchmaker</p>
        <ul class="details__contact">
          <li>Tel. 0492 517 264</li>
          <li>info@tidewellbureau.com.au</li>
          <li>www.tidewellbureau.com.au</li>
        </ul>
      </section>
    </div>
  </article>
</body>
</html>
```